KVT Web Design Project

I would like a simple and elegant design for my international business consulting practice web site. I already have new KVT Logo and will have brochure-colors are blue, green and black

Practice areas:
I offer consulting services specializing in developing Internet-based anti-counterfeiting and anti-fraud programs, test purchases and investigations.

I offer Cyber Security, Data Protection and Compliance services

I also offer International Due Diligence Investigations and Country and Travel Risk Assessments

General Background Investigations

Physical Security Services

About me section listing my Bio

I have a set of key associates that I work with around the world and will want to list their CVs or Bios under "KVT

Associates"Banner with nice photo but not too cluttered

Ability to Upload documents and articles

Contact us section
Updates

I have uploaded my new logo-please advise if you didn't get it or it is not in the correct file format.

Thank you

Dominic

Hello Everyone,

Thank you for your submissions and ideas. I'm not sure about design only vs code. I understand that some of you do not do code-if not then please just provide design.

More about my business: see below link on Google docs to my brochure-this should help but don't use that phone number-see below.

https://files.quillbin.example/view?id=7Qx2Lm9Pz4Rt8Kw3Hn6Vb1Jc5Fd0Sg

 

Here are some details.

Contacts:

Dominic R. Torvello, CPP

President

Torvello and Associates, LLC

P.O. Box 47129

Gaithersburg, MD 20914

USA

web address:www.Torvelloandassociates.example (currently not working)

email:dom @torvelloand associates.example

Tel: 202-555-0173

I hope this is helpful. Dom

Reason: Sorry but during holiday period, have not had as much time to devote to this project. Thanks for your submissions.

Per my previous guidance, please keep designs simple and elegant and free from traditional security images with locks and chains-I prefer one or at most, two photos. Two colors- blue and green in addition to black for print. I want to present professional, corporate and international image. Thank you for your ideas nad submissions.

Dom

Target Market(s)

Law firms, large multi-national corporations, Security Industry

Industry/Entity Type

Business

Requirements
Must have
• Must have sections: (will provide text)

About KVT (will provide text)

Practice areas

Associates (will provide text)

Contact us

(it must also have ability to upload files and articles)
Should not have
• Old style fonts and symbols such as security badges, scales of justice, etc. I want a sleek and modern design.

```html
<!DOCTYPE html>
<html lang="en">
<head>
<meta charset="utf-8">
<title>Torvello &amp; Associates, LLC</title>
<link rel="stylesheet" href="https://fonts.googleapis.com/css2?family=Open+Sans:wght@300;400;600&family=Arimo:wght@400;700&display=swap">
<style>
:root{
  --topbar:#2e2e2e;
  --footer:#2b2b2b;
  --footer-base:#353535;
  --navy:#1d3d6b;
  --brand-blue:#1f5b9e;
  --ink:#1a1a1a;
  --body-grey:#666;
  --footer-link:#8a8a8a;
  --green:#7cc26a;
  --orange:#f0a23a;
  --sky:#4fa3cf;
  --green-tint:#eef4e4;
  --orange-tint:#f7f3e4;
  --sky-tint:#e4f3f3;
  --sidebar:#eeeeee;
  --link:#1d3d6b;
}
*{margin:0;padding:0;box-sizing:border-box}
html,body{width:957px;height:1200px;overflow:hidden;background:#fff}
body{position:relative;font-family:"Arimo",Arial,sans-serif;color:var(--ink)}
.abs{position:absolute}
.head-font{font-family:"Open Sans",Arial,sans-serif}

.topbar{left:0;top:0;width:957px;height:33px;background:var(--topbar);font-family:"Open Sans",sans-serif;font-size:12.5px}
.topbar .account{position:absolute;right:181px;top:9px;color:#9a9a9a}
.topbar .account span{margin:0 4px;color:#777}
.topbar .call{position:absolute;right:37px;top:9px;color:#fff}

.brand{left:42px;top:66px;font-family:"Open Sans",sans-serif;font-size:21px;color:var(--navy);white-space:nowrap}
.tagline{left:42px;top:94px;font-family:"Open Sans",sans-serif;font-size:12.5px;letter-spacing:2.1px;color:var(--brand-blue)}

.nav{left:422px;top:78px;display:flex;font-family:"Open Sans",sans-serif;font-size:14px;color:var(--navy)}
.nav a{color:inherit;text-decoration:none;height:30px;line-height:28px;padding:0 18px 0 19px;border-left:1px solid #d4d4d4}
.nav a.home{border:1px solid #9fb2c7;border-radius:8px;padding:0 13px;height:25px;line-height:22px;margin-top:3px;margin-right:9px}
.nav a.home+a{border-left:none;padding-left:2px}

.hero{left:34px;top:131px;width:886px;height:251px;border-radius:6px;overflow:hidden;
  background:linear-gradient(90deg,#1d4a80 0%,#2d639a 35%,#8aa6bf 52%,#c9c6c0 70%,#e9ddd0 100%);box-shadow:0 6px 8px rgba(0,0,0,.25)}
.hero-copy{left:58px;top:195px;color:#fff;font-family:"Open Sans",sans-serif}
.hero-copy h1{font-weight:400;font-size:23.5px;line-height:33px}
.hero-copy p{font-size:10.5px;line-height:13.5px;margin-top:7px;color:#dfe8f2;width:270px}
.dots{left:55px;top:362px;display:flex;gap:6px}
.dots i{width:9px;height:8px;background:#fff;display:block}

.welcome{left:40px;top:407px;width:585px}
.welcome h2{font-family:"Open Sans",sans-serif;font-weight:400;font-size:18px;color:var(--ink);margin-bottom:12px}
.welcome p{font-size:12px;line-height:14.6px;color:var(--body-grey);margin-bottom:9px}
.welcome p.lead{color:var(--ink);font-size:12.2px}

.btn{display:block;background:linear-gradient(#3a3a3a,#0e0e0e);color:#fff;font-size:11px;border-radius:2px;text-align:center;box-shadow:0 2px 3px rgba(0,0,0,.35)}
.read-btn{left:39px;top:603px;width:68px;height:23px;line-height:23px}
.more-btn{left:28px;top:905px;width:98px;height:22px;line-height:22px}

.offers-title{left:30px;top:657px;font-family:"Open Sans",sans-serif;font-size:17px}
.card{top:687px;height:196px;border-radius:6px 6px 0 0;overflow:hidden}
.card .bar{height:30px;color:#fff;font-size:14px;padding:7px 14px;position:relative}
.card .bar svg{position:absolute;right:12px;top:12px}
.card .body{padding:9px 10px 0 11px;font-size:11.2px;line-height:14.4px;height:166px;position:relative}
.card .body .lead{color:var(--ink);margin-bottom:9px}
.card .body .more{color:var(--body-grey)}
.card .body .link{position:absolute;right:14px;bottom:14px;font-size:10px;color:var(--ink)}
.card .body .link::before{content:"";display:inline-block;border-left:6px solid #111;border-top:4px solid transparent;border-bottom:4px solid transparent;margin-right:5px}
.card-shadow{top:884px;height:10px;background:radial-gradient(ellipse at center,rgba(0,0,0,.18),transparent 70%)}

.sidebar{left:665px;top:382px;width:292px;height:568px;background:linear-gradient(90deg,#e6e6e6,#f7f7f7 30%,#fafafa)}
.why{left:683px;top:412px;width:240px}
.why h3,.testi h3{font-family:"Open Sans",sans-serif;font-weight:400;font-size:17px;margin-bottom:10px}
.why p.intro{font-size:11px;line-height:14px}
.point{position:absolute;left:678px;width:240px;font-size:11px;line-height:14px}
.point svg{position:absolute;left:0;top:0}
.point a{display:block;margin-left:20px;color:var(--link);font-size:12px;text-decoration:underline;margin-bottom:4px}
.point p{margin-left:20px}
.testi{left:696px;top:758px;width:215px}
.testi h3{border-bottom:1px solid #ddd;padding-bottom:4px}
.testi .lead{font-size:12px;line-height:15px;margin-bottom:9px}
.testi .more{font-size:12px;line-height:15px;color:var(--body-grey)}
.testi a{display:block;margin-top:11px;color:#333;font-size:12px;text-decoration:underline}

.footer{left:0;top:950px;width:957px;height:205px;background:var(--footer);font-family:"Open Sans",sans-serif}
.footer h4{font-weight:400;font-size:15.5px;color:#fff;margin-bottom:10px}
.footer ul{list-style:none;font-size:12px;line-height:20.4px;color:var(--footer-link)}
.col{position:absolute;top:26px}
.contact{font-size:12px;line-height:19px;color:#bbb}
.contact u{color:#fff}
.contact .tel{font-size:12px;margin-top:3px}
.contact .tel b{font-weight:400;font-size:15px}
.social{display:flex;align-items:center;gap:6px;margin-top:6px;color:#aaa;font-size:12px}
.social span{margin-right:2px}
.social i{width:20px;height:20px;display:block;border-radius:3px;background:#6d7f94;border:1px solid #ddd}
.base{left:0;top:1155px;width:957px;height:45px;background:var(--footer-base);color:#7a7a7a;font-family:"Open Sans",sans-serif;font-size:10px;padding:13px 0 0 34px}
</style>
</head>
<body>

<div class="abs topbar">
  <div class="account">Sign Up<span>|</span>Register now</div>
  <div class="call">Call us +1800 555 0142</div>
</div>

<div class="abs brand">KVT &nbsp;Torvello &amp; Associates, LLC</div>
<div class="abs tagline">Intellectual Property and Cyber Security</div>

<nav class="abs nav">
  <a class="home" href="#">Home</a>
  <a href="#">About KVT</a>
  <a href="#">Practice Areas</a>
  <a href="#">Associates</a>
  <a href="#">Contact us</a>
</nav>

<div class="abs hero" role="img" aria-label="Banner photograph of business people reviewing work at a laptop"></div>
<div class="abs hero-copy">
  <h1>Get Protect with Our<br>Cyber Security System</h1>
  <p>It's the new way of providing an opportunity to make your products and services available in the global market 24 hours a day through Internet</p>
</div>
<div class="abs dots"><i></i><i></i><i></i><i></i></div>

<section class="abs welcome">
  <h2>Welcome to Torvello &amp; Associates Website</h2>
  <p class="lead">The etymology of "business" relates to the state of being busy either as an individual or society as a whole, doing commercially viable and profitable work.</p>
  <p>The term "business" has at least three usages, depending on the scope — the singular usage (above) to mean a particular company or corporation, the generalized usage to refer to a particular market sector, such as "the music business" and compound forms such as agribusiness, or the broadest meaning to include all activity by the community of suppliers of goods and services.</p>
  <p>Where two or more individuals own a business together but have failed to organize a more specialized form of vehicle, they will be treated as a general partnership. The terms of a partnership are partly governed by a partnership agreement if one is created</p>
</section>
<a class="abs btn read-btn">read more</a>

<h2 class="abs offers-title" style="font-weight:400">What We Offers</h2>

<div class="abs card" style="left:28px;width:200px;background:var(--green-tint)">
  <div class="bar" style="background:var(--green)">Data Protection<svg width="10" height="7"><path d="M0 0h10L5 7z" fill="#fff"/></svg></div>
  <div class="body">
    <p class="lead">A sole proprietorship is a business owned by one person.</p>
    <p class="more">The owner may operate on his or her own or may employ others. The owner of the business has personal liability of the debts incurred by the business.</p>
    <span class="link">READ MORE</span>
  </div>
</div>
<div class="abs card" style="left:236px;width:197px;background:var(--orange-tint)">
  <div class="bar" style="background:var(--orange)">Background Investigation<svg width="10" height="7"><path d="M0 0h10L5 7z" fill="#fff"/></svg></div>
  <div class="body">
    <p class="lead">Background Investigations: A sole proprietorship is a business owned by one person.</p>
    <p class="more">A corporation is owned by multiple shareholders and is overseen by a board of directors, which hires the business's managerial staff.</p>
    <span class="link">READ MORE</span>
  </div>
</div>
<div class="abs card" style="left:443px;width:197px;background:var(--sky-tint)">
  <div class="bar" style="background:var(--sky)">Physical Data Protection<svg width="10" height="7"><path d="M0 0h10L5 7z" fill="#fff"/></svg></div>
  <div class="body">
    <p class="lead">A sole proprietorship is a business owned by one person.</p>
    <p class="more">The owner may operate on his or her own or may employ others. The owner of the business has personal liability</p>
    <span class="link">READ MORE</span>
  </div>
</div>
<div class="abs card-shadow" style="left:40px;width:176px"></div>
<div class="abs card-shadow" style="left:248px;width:173px"></div>
<div class="abs card-shadow" style="left:455px;width:173px"></div>
<a class="abs btn more-btn">more services</a>

<aside class="abs sidebar"></aside>
<div class="abs why">
  <h3>Why Choose Us ?</h3>
  <p class="intro">Many businesses are operated through a separate entity such as a corporation or a partnership (either formed with or without limited liability).</p>
</div>
<div class="point" style="top:519px;left:681px">
  <svg width="14" height="12"><rect x="0.5" y="2.5" width="9" height="9" fill="#fff" stroke="#999"/><path d="M2 6l3 3 8-8" fill="none" stroke="#667" stroke-width="1.6"/></svg>
  <a href="#" style="margin-left:22px">Heading here</a>
  <p style="margin-left:22px">A single person who owns and runs a business is commonly known as a sole proprietor.</p>
</div>
<div class="point" style="top:600px">
  <svg width="14" height="12"><rect x="0.5" y="2.5" width="9" height="9" fill="#fff" stroke="#999"/><path d="M2 6l3 3 8-8" fill="none" stroke="#667" stroke-width="1.6"/></svg>
  <a href="#">Heading here</a>
  <p>A different concept is the value-based marketing which states the role of marketing.</p>
</div>
<div class="point" style="top:672px">
  <svg width="14" height="12"><rect x="0.5" y="2.5" width="9" height="9" fill="#fff" stroke="#999"/><path d="M2 6l3 3 8-8" fill="none" stroke="#667" stroke-width="1.6"/></svg>
  <a href="#">Heading here</a>
  <p>A different concept is the value-based marketing which states the role of marketing.</p>
</div>
<div class="abs testi">
  <h3>Testimonials</h3>
  <p class="lead">Marketing evolved to meet the stasis in developing new markets</p>
  <p class="more">The adoption of marketing strategies requires businesses to shift their focus from production</p>
  <a href="#">read more</a>
</div>

<footer class="abs footer">
  <div class="col" style="left:38px">
    <h4>Links</h4>
    <ul><li>About Our Company</li><li>Featured Services</li><li>Parnters</li><li>Clients &amp; Partners</li><li>Contact info</li></ul>
  </div>
  <div class="col" style="left:243px">
    <h4>Services We Offer</h4>
    <ul><li>Cyber Security</li><li>General Background Investigations</li><li>Data Protection</li><li>Physical Security Services.</li></ul>
  </div>
  <div class="col contact" style="left:502px;top:24px">
    <h4>Contact Information</h4>
    <u>KVT Associates Inc</u><br>C-4/218 Sec-12, Harrow Park<br>New Delhi
    <div class="tel">Tele <b>+1800 555 0187</b></div>
    <div class="social" style="margin-left:-2px"><span>Connect with us</span><i></i><i></i><i></i><i></i></div>
  </div>
</footer>
<div class="abs base">copyright © 2011 company name All right reserved</div>

</body>
</html>
```